Business Cards for new orthopaedic surgery practice

My husband and I are starting our own orthopaedic surgery practice. We are looking for a business card that is uniform, but one will have my name/title and the other will have his. You can just create one design with my name on it for now. But when I choose your design as the winning design I will ask that you add another copy with his name/title.

We are looking for classy, simple, elite all in one. We like dark blues/a little gold/yellow. Something that goes with our logo. We want our logo incorporated. Here is all the info you need:
Business name: RV Bone & Vitality Center
Location: 38517 North Willowmere Ave
Lindale Grove, FL 33990
Phone: 954-218-4063
Fax: 954-582-7341
Email: info@myrvbonecare.example

Names: Lydia Vance, M.D.
Board Certified Hand and Upper Extremity Surgeon

Ebo Dansu, M.D.
Board Certified Hip & Knee Replacement/General Orthopaedic Surgeon

Can decide what you want to put on the back. Maybe a slogan:
Rooted in Care. Focused on You

I am just going to upload our logo. The only thing is if we select you as the winning design, the location, and phone numbers may change. We will need your help to update that once fully solidified.

Industry/Entity Type

Medical

Contact Information for Business Card

Colors
0054AA
0677BA
7BADD7
CADEEF
E8F1F8
0094D4
00A9DD
6FCCEA
C7EBF8
E9F6FB

Requirements
Must have
• class, appeal,
Should not have
• We want to air on the side of masculine if we are looking at masculine vs. feminine feel. But we still want it classy, sophisticated, and something we will love

```html
<!DOCTYPE html>
<html lang="en">
<head>
<meta charset="utf-8">
<title>RV Bone &amp; Vitality Center – Business Card</title>
<link rel="stylesheet" href="https://fonts.googleapis.com/css2?family=Cinzel:wght@600&family=Lato:wght@400;700&display=swap">
<style>
  :root {
    --backdrop: #8c8c8c;
    --paper: #ffffff;
    --navy-deep: #14266b;
    --navy: #22408a;
    --navy-text: #263f8c;
    --cyan: #1fb6e0;
    --white: #ffffff;
  }
  * { box-sizing: border-box; margin: 0; padding: 0; }
  html, body {
    width: 1200px; height: 1200px; overflow: hidden;
    background: var(--backdrop);
  }
  .card {
    position: absolute; left: 242px;
    width: 717px; height: 438px;
    background: var(--paper);
    overflow: hidden;
  }
  .card--front { top: 114px; }
  .card--back { top: 647px; }
  .wave { position: absolute; inset: 0; width: 100%; height: 100%; }

  .brand-name {
    position: absolute; left: 0; right: 0; top: 128px;
    text-align: center;
    font-family: "Cinzel", serif; font-weight: 600;
    font-size: 40px; line-height: 1.15; letter-spacing: 0.5px;
    color: var(--navy-text);
  }

  .doctor {
    position: absolute; left: 0; right: 0; top: 62px;
    text-align: center; font-family: "Lato", sans-serif;
  }
  .doctor__name {
    font-weight: 700; font-size: 17px; color: var(--cyan);
    letter-spacing: 0.2px; margin-bottom: 4px;
  }
  .doctor__title {
    font-size: 13.5px; line-height: 18px; color: var(--navy-text);
  }

  .back-brand {
    position: absolute; left: 120px; width: 222px; top: 236px;
    text-align: center;
    font-family: "Cinzel", serif; font-weight: 600;
    font-size: 24px; line-height: 1.2; color: var(--white);
  }
  .divider {
    position: absolute; left: 357px; top: 204px;
    width: 1.5px; height: 149px; background: var(--white);
  }
  .contact {
    position: absolute; left: 400px; top: 216px;
    list-style: none; font-family: "Lato", sans-serif;
    font-size: 14px; color: var(--white);
  }
  .contact__item {
    display: flex; align-items: flex-start; gap: 12px;
    height: 31px; line-height: 18px;
  }
  .contact__icon { width: 15px; height: 15px; flex: none; margin-top: 1px; fill: var(--cyan); }
</style>
</head>
<body>

<section class="card card--front" aria-label="Card front">
  <svg class="wave" viewBox="0 0 872 533" preserveAspectRatio="none" aria-hidden="true">
    <defs>
      <linearGradient id="bandFront" x1="0" x2="1" y1="0" y2="0">
        <stop offset="0" stop-color="#15286e"/>
        <stop offset="0.2" stop-color="#22408a"/>
        <stop offset="0.8" stop-color="#22408a"/>
        <stop offset="1" stop-color="#15286e"/>
      </linearGradient>
    </defs>
    <path fill="var(--navy-deep)" d="M0,350 C40,336 90,322 120,328 C165,337 180,378 230,400 C320,440 380,444 436,443 C520,441 600,420 680,382 C730,352 742,330 790,330 C830,330 858,345 872,358 L872,533 L0,533 Z"/>
    <path fill="url(#bandFront)" d="M0,372 C40,356 90,344 120,348 C165,356 185,394 235,414 C320,448 380,454 436,453 C520,452 600,434 680,400 C730,372 745,350 790,350 C830,350 858,364 872,376 L872,533 L0,533 Z"/>
  </svg>
  <p class="brand-name">RV Bone &amp; Vitality<br>Center</p>
</section>

<section class="card card--back" aria-label="Card back">
  <svg class="wave" viewBox="0 0 872 533" preserveAspectRatio="none" aria-hidden="true">
    <defs>
      <linearGradient id="bandBack" x1="0" x2="1" y1="0" y2="0">
        <stop offset="0" stop-color="#15286e"/>
        <stop offset="0.2" stop-color="#22408a"/>
        <stop offset="0.8" stop-color="#22408a"/>
        <stop offset="1" stop-color="#15286e"/>
      </linearGradient>
    </defs>
    <path fill="var(--navy-deep)" d="M0,80 C40,70 90,58 120,64 C165,72 180,110 230,132 C320,170 380,176 436,175 C520,173 600,152 680,114 C730,84 742,62 790,62 C830,62 858,76 872,90 L872,533 L0,533 Z"/>
    <path fill="url(#bandBack)" d="M0,100 C40,90 90,80 120,84 C165,92 185,128 235,148 C320,182 380,188 436,187 C520,186 600,166 680,132 C730,104 745,82 790,82 C830,82 858,96 872,108 L872,533 L0,533 Z"/>
  </svg>

  <div class="doctor">
    <p class="doctor__name">LYDIA VANCE, M.D.</p>
    <p class="doctor__title">Board Certified Hand and<br>Upper Extremity Surgeon</p>
  </div>

  <p class="back-brand">RV Bone &amp;<br>Vitality Center</p>
  <div class="divider"></div>

  <ul class="contact">
    <li class="contact__item">
      <svg class="contact__icon" viewBox="0 0 24 24" aria-hidden="true"><path d="M6.6 10.8a15.1 15.1 0 0 0 6.6 6.6l2.2-2.2a1 1 0 0 1 1-.25 11.4 11.4 0 0 0 3.6.57 1 1 0 0 1 1 1V20a1 1 0 0 1-1 1A17 17 0 0 1 3 4a1 1 0 0 1 1-1h3.5a1 1 0 0 1 1 1c0 1.25.2 2.45.57 3.6a1 1 0 0 1-.25 1z"/></svg>
      <span>954-218-4063</span>
    </li>
    <li class="contact__item">
      <svg class="contact__icon" viewBox="0 0 24 24" aria-hidden="true"><path d="M6 2h12v5H6zM4 8h16a2 2 0 0 1 2 2v6h-4v-3H6v3H2v-6a2 2 0 0 1 2-2zm3 6h10v8H7z"/></svg>
      <span>954-582-7341</span>
    </li>
    <li class="contact__item">
      <svg class="contact__icon" viewBox="0 0 24 24" aria-hidden="true"><path d="M2 8l10-6 10 6v12H2zm2 1.2V18h16V9.2l-8 5z"/></svg>
      <span>info@myrvbonecare.example</span>
    </li>
    <li class="contact__item">
      <svg class="contact__icon" viewBox="0 0 24 24" aria-hidden="true"><path d="M12 2a7 7 0 0 0-7 7c0 5.2 7 13 7 13s7-7.8 7-13a7 7 0 0 0-7-7zm0 9.5A2.5 2.5 0 1 1 12 6.5a2.5 2.5 0 0 1 0 5z"/></svg>
      <span>38517 North Willowmere Ave<br>Lindale Grove, FL 33990</span>
    </li>
  </ul>
</section>

</body>
</html>
```